Visitenkartenvorlage ändern
Zielgruppe
Eventmanagement
Aufgabenstellung
Die beiliegende Visitenkarte wäre das "perfekte" Logo für mich. Da es sich hierbei aber um eine Vorlage eines Online-Druck-Anbieters handelt, darf es leider nur für deren Drucke verwendet werden und nicht für Printwerbung, Homepage etc. Daher sollte es genügend verfremdet werden, so dass ich es verwenden kann.

```html
<!DOCTYPE html>
<html lang="de">
<head>
<meta charset="utf-8">
<title>Gut Geplant – Visitenkarte</title>
<link rel="stylesheet" href="https://fonts.googleapis.com/css2?family=Marcellus&family=Great+Vibes&display=swap">
<style>
  :root {
    --backdrop: #0f1142;
    --card: #a7a7a9;
    --card-edge: #9c9c9f;
    --ink: #333336;
    --swirl-light: rgba(205, 205, 210, 0.55);
  }
  * { margin: 0; padding: 0; box-sizing: border-box; }
  html, body {
    width: 1200px;
    height: 1200px;
    overflow: hidden;
    background: var(--backdrop);
  }
  .canvas {
    position: relative;
    width: 1200px;
    height: 1200px;
  }
  .card {
    position: absolute;
    left: 294px;
    width: 614px;
    height: 411px;
    background: var(--card);
    border: 1px solid var(--card-edge);
    color: var(--ink);
    font-family: "Marcellus", "Trajan Pro", serif;
    text-align: center;
  }
  .card--front { top: 166px; }
  .card--back { top: 623px; overflow: hidden; }

  .brand-name {
    position: absolute;
    left: 0; right: 0;
    font-weight: 400;
    letter-spacing: 0.02em;
  }
  .card--front .brand-name { top: 42px; font-size: 42px; }
  .card--back .brand-name { top: 150px; font-size: 30px; }

  .brand-mark {
    position: absolute;
    left: 50%;
    transform: translateX(-50%);
  }
  .card--front .brand-mark { top: 138px; }
  .card--back .brand-mark { top: 32px; }

  .tagline {
    position: absolute;
    left: 0; right: 0;
    letter-spacing: 0.02em;
  }
  .card--front .tagline { top: 223px; font-size: 28px; }
  .card--back .tagline { top: 191px; font-size: 21px; }

  .website {
    position: absolute;
    left: 0; right: 0;
    top: 286px;
    font-size: 18px;
  }

  .swirl-field {
    position: absolute;
    left: 0;
    top: 90px;
    width: 614px;
    height: 260px;
    background:
      radial-gradient(ellipse 120px 90px at 80px 130px, var(--swirl-light), transparent 70%),
      radial-gradient(ellipse 150px 110px at 470px 110px, var(--swirl-light), transparent 70%),
      radial-gradient(ellipse 90px 70px at 300px 230px, rgba(205,205,210,0.35), transparent 70%);
  }

  .person-name {
    position: absolute;
    left: 0; right: 0;
    top: 238px;
    font-family: "Great Vibes", cursive;
    font-size: 50px;
    font-weight: 400;
  }

  .contact {
    position: absolute;
    left: 72px;
    top: 337px;
    display: flex;
    gap: 36px;
    font-size: 19px;
    list-style: none;
  }
</style>
</head>
<body>
<main class="canvas">

  <section class="card card--front" aria-label="Vorderseite">
    <h1 class="brand-name">GUT GEPLANT</h1>
    <svg class="brand-mark" width="56" height="56" viewBox="0 0 56 56" aria-hidden="true">
      <circle cx="28" cy="28" r="25" fill="none" stroke="var(--ink)" stroke-width="2"/>
    </svg>
    <p class="tagline">EVENTS UND MEHR</p>
    <p class="website">www.gut-geplant.de</p>
  </section>

  <section class="card card--back" aria-label="Rückseite">
    <div class="swirl-field" role="img" aria-label="Zartes helles Rankenmuster im Hintergrund"></div>
    <svg class="brand-mark" width="56" height="56" viewBox="0 0 56 56" aria-hidden="true">
      <circle cx="28" cy="28" r="25" fill="none" stroke="var(--ink)" stroke-width="2"/>
    </svg>
    <h2 class="brand-name">GUT GEPLANT</h2>
    <p class="tagline">EVENTS UND MEHR</p>
    <p class="person-name">Marlene Vossberg</p>
    <ul class="contact">
      <li class="contact-email">info@gut-geplant.de</li>
      <li class="contact-phone">+49 761 204387</li>
    </ul>
  </section>

</main>
</body>
</html>
```